Kelvor Engineers: Why you should hire us keepsake

New design. Open to plastic cards. We are an engineering firm that designs cell phone towers and commercial buildings. Please check out our website www.kelvorstruct.com for more details. We want people to remember our card and for it to be useful if possible. We want the same look and feel on these cards to be translated to other marketing material we may need such as brochures.

Target Market(s)

Architects, Developers and Telecommunication Carriers

Industry/Entity Type

Engineering

Contact Information for Business Card

Card with our company colors, logo, and innovative design with elements related to our industry.

Font styles to use
Sans Serif

Colors
9bcb3c
abd036
0255a3

Requirements
Must have
• Sleek and hip design
Nice to have
• Bright lime green and navy coloring that pops with an innovative design.
Should not have
• A basic and boring design

```html
<!DOCTYPE html>
<html lang="en">
<head>
<meta charset="utf-8">
<title>Kelvor Engineers – Business Card</title>
<link href="https://fonts.googleapis.com/css2?family=Roboto:wght@400;500;700&family=Roboto+Condensed:wght@700&display=swap" rel="stylesheet">
<style>
  :root {
    --backdrop: #2b2b2b;
    --card-white: #f3f3f3;
    --lime: #00ff00;
    --navy: #022c5b;
    --grey-text: #555555;
    --white: #ffffff;
  }
  * { margin: 0; padding: 0; box-sizing: border-box; }
  html, body { width: 1200px; height: 960px; overflow: hidden; }
  body { background: var(--backdrop); position: relative; font-family: "Roboto", sans-serif; }

  .card {
    position: absolute;
    left: 320px;
    width: 600px;
    height: 342px;
    border-radius: 20px;
    overflow: hidden;
  }
  .card--front { top: 105px; background: var(--card-white); }
  .card--back { top: 493px; background: var(--lime); }

  .brand-name {
    position: absolute;
    top: 135px;
    left: 0; right: 0;
    text-align: center;
    font-family: "Roboto Condensed", sans-serif;
    font-weight: 700;
    font-size: 56px;
    line-height: 1;
    color: var(--lime);
  }
  .tagline {
    position: absolute;
    top: 269px;
    left: 0; right: 0;
    display: flex;
    justify-content: center;
    align-items: center;
    gap: 3px;
    font-family: "Roboto", sans-serif;
    font-weight: 700;
    font-size: 15px;
    line-height: 20px;
    color: var(--lime);
  }
  .tagline::before, .tagline::after {
    content: "";
    width: 28px;
    height: 2px;
    background: var(--navy);
  }
  .locations {
    position: absolute;
    top: 290px;
    left: 0; right: 0;
    text-align: center;
    font-size: 15px;
    line-height: 20px;
    letter-spacing: 0.4px;
    color: var(--grey-text);
  }

  .pattern-area { position: absolute; left: 0; top: 0; }

  .contact-block { position: absolute; left: 338px; top: 182px; }
  .person-name {
    font-family: "Roboto Condensed", sans-serif;
    font-weight: 700;
    font-size: 21px;
    line-height: 24px;
    color: var(--navy);
    margin-bottom: 10px;
  }
  .contact-list { list-style: none; }
  .contact-list li {
    display: flex;
    align-items: center;
    gap: 8px;
    height: 19px;
    font-size: 14px;
    color: var(--white);
  }
  .contact-list svg { width: 14px; height: 14px; fill: var(--navy); flex: none; }
</style>
</head>
<body>

  <section class="card card--front">
    <div class="brand-name">Kelvor Engineers</div>
    <div class="tagline">MULTI-DISCIPLINE ENGINEERING</div>
    <div class="locations">Carvale | Dunmore Bay | Westrick | Pell Harbor</div>
  </section>

  <section class="card card--back">
    <svg class="pattern-area" width="440" height="342" viewBox="0 0 440 342" role="img" aria-label="Stepped checkerboard pattern in navy and lime">
      <defs>
        <linearGradient id="stepFill" x1="0" y1="0" x2="1" y2="1">
          <stop offset="0" stop-color="#0d6e3c"/>
          <stop offset="1" stop-color="#12a53a"/>
        </linearGradient>
      </defs>
      <polygon fill="url(#stepFill)" points="0,0 440,0 440,47 392,47 392,95 343,95 343,144 293,144 293,195 244,195 244,244 196,244 196,294 148,294 148,342 0,342"/>
    </svg>

    <div class="contact-block">
      <h1 class="person-name">DANA HOLLOWAY REYES</h1>
      <ul class="contact-list">
        <li>
          <svg viewBox="0 0 24 24"><path d="M6.6 10.8a15.1 15.1 0 0 0 6.6 6.6l2.2-2.2a1 1 0 0 1 1-.25 11.4 11.4 0 0 0 3.6.57 1 1 0 0 1 1 1V20a1 1 0 0 1-1 1A17 17 0 0 1 3 4a1 1 0 0 1 1-1h3.5a1 1 0 0 1 1 1c0 1.25.2 2.450.57 3.57a1 1 0 0 1-.25 1z"/></svg>
          555.210.4417
        </li>
        <li>
          <svg viewBox="0 0 24 24"><path d="M7 1h10a2 2 0 0 1 2 2v18a2 2 0 0 1-2 2H7a2 2 0 0 1-2-2V3a2 2 0 0 1 2-2zm0 3v14h10V4zm5 15.5a1.2 1.2 0 1 0 0 2.4 1.2 1.2 0 0 0 0-2.4z"/></svg>
          555.384.9062
        </li>
        <li>
          <svg viewBox="0 0 24 24"><path d="M2 5h20v14H2zm2 2v.5l8 5 8-5V7zm0 2.8V17h16V9.8l-8 5z"/></svg>
          dreyes@kelvorstruct.com
        </li>
        <li>
          <svg viewBox="0 0 24 24"><path d="M12 2a10 10 0 1 0 0 20 10 10 0 0 0 0-20zm-1 17.9A8 8 0 0 1 4.2 10.6L9 15.4v1a2 2 0 0 0 2 2zm6.9-2.5A2 2 0 0 0 16 16h-1v-3a1 1 0 0 0-1-1H8v-2h2a1 1 0 0 0 1-1V7h2a2 2 0 0 0 2-2v-.4a8 8 0 0 1 2.9 12.8z"/></svg>
          www.kelvorstruct.com
        </li>
      </ul>
    </div>
  </section>

</body>
</html>
```